Moxy Fen needs some awesome stationary

Do you have what it takes to get my brand? You either do or you don't, have a crack at a design and you my just win my business.

I don't want to waste your or my time, so put your creative genius on either a business card or envelope.

I however need a package of stationary that follows the same brand. I will message you to complete the remaining should I like your first submission.

Here is what I need, have a go!

Basically I need the following for my small business based in melbourne.
- Letterhead (printer ready and MS Word)
- Business Card
- Compliments Slip
- Envelope
- Proposal Cover Page (MS Word only)
- Presentation Folder
- Marbled Fox Cards
- Student Name Tent
- Index Cards
- Vell-Ka

I am establishing the brand and it must be modern, professional but also relaxed; that is not formal and not corporate. It represents a company are leaders, but small enough to care and operate like a bunch of friends. We are bringing people and conversations back to business, and turfing out all the bureaucracy and crazy and wasteful procedures. Its about "lets talk and figure it out together and find even better ways".

Target Market(s)

Mainly companies that build software products, but Agile practices are used in many other industries (even graphic design projects)

Industry/Entity Type

Information Technology

Font styles to use
Sans Serif

Colors
3176b5
aaaaaa

Requirements
Must have
• I like curves and circles and not boxes or rectangles.
• I want a colour rich design with my brand colours, but it must be balanced.
• I want more modern than traditional, but simple modern
Should not have
• Not corporate
• Please don't waste my time if your not going to think about it.
• Don't mess with my primary logo
• Don't change my colours
• Don't overlay logo on image

```html
<!DOCTYPE html>
<html lang="en">
<head>
<meta charset="utf-8">
<title>Moxy Fen — Business Card</title>
<link rel="stylesheet" href="https://fonts.googleapis.com/css2?family=Open+Sans:wght@400;600&family=Josefin+Sans:wght@600&display=swap">
<style>
  :root {
    --page: #e9ebef;
    --navy: #263a5e;
    --navy-deep: #1f3152;
    --band: #3a63a8;
    --brand-blue: #3176b5;
    --brand-grey: #aaaaaa;
    --white: #ffffff;
    --text-soft: #dfe5ef;
  }
  * { box-sizing: border-box; margin: 0; padding: 0; }
  html, body { width: 1200px; height: 800px; overflow: hidden; }
  body {
    background: var(--page);
    font-family: "Open Sans", sans-serif;
    display: flex;
    align-items: center;
    justify-content: center;
    gap: 40px;
  }
  .card {
    position: relative;
    width: 540px;
    height: 310px;
    background: var(--navy);
    border-radius: 6px;
    overflow: hidden;
    box-shadow: 0 10px 30px rgba(20, 30, 50, 0.25);
  }
  .band {
    position: absolute;
    left: 0;
    right: 0;
    background: var(--band);
  }
  .brand-mark {
    position: absolute;
    display: flex;
    align-items: center;
    gap: 10px;
    color: var(--white);
    font-weight: 600;
    white-space: nowrap;
  }
  .brand-dot {
    border-radius: 50%;
    background: var(--white);
    flex: none;
  }

  /* Front */
  .card--front .band { top: 108px; height: 100px; }
  .card--front .brand-mark {
    left: 0; right: 0; top: 60px;
    flex-direction: column;
    gap: 16px;
    font-size: 34px;
  }
  .card--front .brand-dot { width: 66px; height: 66px; }
  .card--front .notch {
    position: absolute;
    left: 262px; bottom: 18px;
    width: 16px; height: 10px;
    background: var(--brand-blue);
    border-radius: 8px 8px 2px 2px;
  }

  /* Back */
  .card--back .band { top: 28px; height: 92px; }
  .card--back .brand-dot {
    position: absolute;
    left: 48px; top: 26px;
    width: 96px; height: 96px;
    background: var(--white);
    border-radius: 50%;
  }
  .card--back .brand-mark {
    right: 42px; top: 80px;
    font-size: 32px;
  }
  .person {
    position: absolute;
    left: 30px; top: 150px;
    color: var(--white);
  }
  .person__name {
    font-family: "Josefin Sans", sans-serif;
    font-size: 19px;
    font-variant: small-caps;
    letter-spacing: 2.5px;
  }
  .person__title {
    font-size: 10px;
    color: var(--text-soft);
    margin-top: 2px;
  }
  .icon-rail {
    position: absolute;
    left: 232px; top: 150px;
    width: 16px; height: 130px;
    background: var(--band);
    border-radius: 8px;
    display: flex;
    flex-direction: column;
    align-items: center;
    justify-content: space-around;
    padding: 8px 0;
  }
  .icon-rail svg { width: 10px; height: 10px; fill: var(--white); }
  .contact-list {
    position: absolute;
    left: 262px; top: 160px;
    list-style: none;
    color: var(--text-soft);
    font-size: 11.5px;
    line-height: 20px;
  }
</style>
</head>
<body>

  <section class="card card--front" aria-label="Business card front">
    <div class="band"></div>
    <div class="brand-mark">
      <span class="brand-dot"></span>
      <span class="brand-name">Moxy Fen</span>
    </div>
    <span class="notch"></span>
  </section>

  <section class="card card--back" aria-label="Business card back">
    <div class="band"></div>
    <span class="brand-dot"></span>
    <div class="brand-mark"><span class="brand-name">Moxy Fen</span></div>

    <div class="person">
      <p class="person__name">Dara Quillon</p>
      <p class="person__title">CEO, Professional Scrum Trainer</p>
    </div>

    <div class="icon-rail" aria-hidden="true">
      <svg viewBox="0 0 10 10"><path d="M5 0a3.5 3.5 0 0 1 3.5 3.5C8.5 6 5 10 5 10S1.5 6 1.5 3.5A3.5 3.5 0 0 1 5 0zm0 2a1.5 1.5 0 1 0 0 3 1.5 1.5 0 0 0 0-3z"/></svg>
      <svg viewBox="0 0 10 10"><path d="M2 0l2 2.5-1.2 1.3a6 6 0 0 0 3.4 3.4L7.5 6 10 8l-1.5 2C4 10 0 6 0 1.5z"/></svg>
      <svg viewBox="0 0 10 10"><rect x="2.5" y="0" width="5" height="10" rx="1"/></svg>
      <svg viewBox="0 0 10 10"><path d="M0 2h10v6H0z M0 2l5 3.5L10 2" stroke="#3a63a8" stroke-width="0.8"/></svg>
      <svg viewBox="0 0 10 10"><circle cx="5" cy="5" r="4.5" fill="none" stroke="#fff" stroke-width="1"/><path d="M0.5 5h9M5 0.5v9" stroke="#fff" stroke-width="0.8"/></svg>
    </div>

    <ul class="contact-list">
      <li>PO Box 4170, Elmsford Vale, VIC 3990, Australia</li>
      <li>1300MOXYF</li>
      <li>+61 400 217 563</li>
      <li>dara@moxyfen.com.au</li>
      <li>www.moxyfen.com.au</li>
    </ul>
  </section>

</body>
</html>
```